design a construction company business card

Design business card around our logo. Card must have all the typical info: name, title, address, phone, email, business name, etc. Somewhere on the card I would like to see our motto "Grounded in trust... Driven by dedication." Consider adding a splash of bright orange to the card to complement the blues and silvers/grays in the logo. We are open to metallic inks, textures, etc. We would like to see options on both light and dark backgrounds. The font in the logo is Euro Technic Extended Regular.

```html
<!DOCTYPE html>
<html lang="en">
<head>
<meta charset="utf-8">
<title>Halden Contracting – Business Card</title>
<link href="https://fonts.googleapis.com/css2?family=Michroma&family=Montserrat:wght@400;500&display=swap" rel="stylesheet">
<style>
  :root {
    --backdrop: #1c1c1e;
    --card: #0c0c0d;
    --card-edge: #1a1a1c;
    --foil: #c9c9cc;
    --foil-soft: #8d8d92;
    --ink-gloss: #4a4a4f;
  }
  * { margin: 0; padding: 0; box-sizing: border-box; }
  html, body { width: 1200px; height: 913px; overflow: hidden; }
  body {
    background: var(--backdrop);
    display: flex;
    align-items: center;
    justify-content: center;
    gap: 60px;
    font-family: "Montserrat", sans-serif;
  }
  .card {
    width: 525px;
    height: 300px;
    background: var(--card);
    border: 1px solid var(--card-edge);
    display: flex;
    flex-direction: column;
    align-items: center;
    justify-content: center;
    text-align: center;
  }
  .brand-name {
    font-family: "Montserrat", sans-serif;
    font-weight: 500;
    font-size: 28px;
    letter-spacing: 1px;
    color: var(--foil);
    line-height: 1.2;
  }
  .contact-back { padding-top: 10px; }
  .back-mark {
    font-family: "Montserrat", sans-serif;
    font-weight: 500;
    font-size: 18px;
    letter-spacing: 1px;
    color: var(--foil);
    margin-bottom: 18px;
  }
  .person-name {
    font-family: "Michroma", sans-serif;
    font-size: 15px;
    letter-spacing: 1.5px;
    color: var(--foil-soft);
  }
  .person-title {
    font-size: 10px;
    letter-spacing: 2px;
    color: var(--foil-soft);
    margin-top: 4px;
    margin-bottom: 30px;
    text-transform: uppercase;
  }
  .details {
    font-size: 9.5px;
    letter-spacing: 1px;
    line-height: 1.9;
    color: var(--ink-gloss);
    text-transform: uppercase;
  }
  .motto {
    font-size: 10px;
    letter-spacing: 0.5px;
    color: var(--ink-gloss);
    margin-top: 4px;
  }
</style>
</head>
<body>
  <section class="card brand-front">
    <div class="brand-name">Halden Contracting, Inc.</div>
  </section>

  <section class="card contact-back">
    <div class="back-mark">Halden Contracting, Inc.</div>
    <div class="person-name">MARCUS REED</div>
    <div class="person-title">President</div>
    <div class="details">
      4120 Birchwood Lane, Juneau, Alaska 99801<br>
      555-210-7788 &nbsp;|&nbsp; marcus@halden.com &nbsp;|&nbsp; www.halden.com
    </div>
    <div class="motto">Grounded in trust... Driven by dedication.</div>
  </section>
</body>
</html>
```